Business Card Design

Attached is my current Business card I do not like it but I must save the logo portion of it. Don't like the color or the lettering am looking for more architectural look in grays or taupe with the green more of a charturese color and the blue a charcoal color on a textured paper that looks more like something high-end that would appeal to an architect or a designer. We make concrete decorative items such as concrete fireplaces, sinks, tops and more.

Target Market(s)

Architects designers of Commercial and Residential - artistic features

Industry/Entity Type

Architect

Contact Information for Business Card

Marisol T. Quenby President and Marketing Director
602-418-5093
email marisol@vantorelstone.example
Showroom "Quillmont Design Center" 4183 W Palomar Scottsdale AZ
Fax: 602-731-6624

Font styles to use
Sans Serif

Requirements
Must have
• Architectural
Natural and earthy colors with a touch of color in the existing attached

```html
<!DOCTYPE html>
<html lang="en">
<head>
<meta charset="utf-8">
<title>Vantorel Stone — Business Card</title>
<link href="https://fonts.googleapis.com/css2?family=Open+Sans:wght@300;400;600;700&display=swap" rel="stylesheet">
<style>
  :root {
    --charcoal: #3a3c3f;
    --chartreuse: #a8c23a;
    --taupe: #b9b29f;
    --paper: #f7f5f0;
    --ink: #3a3c3f;
    --ink-soft: #5e5b55;
    --brand-grey: #7c776b;
    --on-dark: #f4f2ec;
    --backdrop: #e4e2dc;
  }
  * { margin: 0; padding: 0; box-sizing: border-box; }
  html, body {
    width: 1200px; height: 865px; overflow: hidden;
    background: var(--backdrop);
    font-family: "Open Sans", Arial, sans-serif;
  }
  .canvas {
    position: relative; width: 1200px; height: 865px;
    display: flex; flex-direction: column; align-items: center; justify-content: center; gap: 36px;
  }
  .card {
    position: relative; width: 680px; height: 389px; overflow: hidden;
    box-shadow: 0 6px 18px rgba(0,0,0,0.18);
  }
  .card__ground { position: absolute; inset: 0; width: 100%; height: 100%; }

  /* Front */
  .holder {
    position: absolute; right: 34px; top: 26px; text-align: right; color: var(--ink);
  }
  .holder__name { font-weight: 700; font-size: 24px; letter-spacing: 0.5px; text-transform: uppercase; }
  .holder__title { font-weight: 400; font-size: 15px; color: var(--ink-soft); margin-top: -2px; }
  .brand {
    position: absolute; left: 110px; top: 96px;
    display: flex; align-items: center; gap: 14px;
  }
  .brand__square { width: 22px; height: 22px; background: var(--chartreuse); }
  .brand__name {
    font-weight: 300; font-size: 46px; color: var(--brand-grey); letter-spacing: 0.5px;
  }
  .address {
    position: absolute; left: 34px; top: 180px;
    display: flex; align-items: flex-start; gap: 10px;
    font-size: 17px; line-height: 1.25; color: var(--ink);
  }
  .contact {
    position: absolute; color: var(--on-dark); font-size: 15px; font-weight: 600;
    display: flex; flex-direction: column; gap: 12px;
  }
  .contact--left { left: 34px; top: 318px; }
  .contact--right { left: 380px; top: 290px; }
  .contact__row { display: flex; align-items: center; gap: 10px; }
  .icon { width: 16px; height: 16px; flex: none; }
</style>
</head>
<body>
<main class="canvas">

  <section class="card card--front" aria-label="Business card front">
    <svg class="card__ground" viewBox="0 0 680 389" preserveAspectRatio="none" aria-hidden="true">
      <rect width="680" height="389" fill="var(--charcoal)"/>
      <polygon points="0,0 680,0 680,230 0,300" fill="var(--paper)"/>
      <polygon points="0,300 680,230 680,240 0,310" fill="var(--taupe)"/>
    </svg>

    <div class="holder">
      <div class="holder__name">Marisol T. Quenby</div>
      <div class="holder__title">President and Marketing Director</div>
    </div>

    <div class="brand">
      <span class="brand__square"></span>
      <span class="brand__name">Vantorel Stone</span>
    </div>

    <div class="address">
      <svg class="icon" viewBox="0 0 16 16" aria-hidden="true" style="width:18px;height:22px">
        <path d="M8 0C4.7 0 2.2 2.5 2.2 5.7 2.2 10 8 16 8 16s5.8-6 5.8-10.3C13.8 2.5 11.3 0 8 0z" fill="var(--ink)"/>
        <circle cx="8" cy="5.8" r="2.2" fill="var(--paper)"/>
      </svg>
      <div>Quillmont Design Center<br>4183 W Palomar, Scottsdale AZ</div>
    </div>

    <div class="contact contact--left">
      <div class="contact__row">
        <svg class="icon" viewBox="0 0 16 16" aria-hidden="true">
          <rect x="4" y="1" width="8" height="14" rx="1.5" fill="none" stroke="var(--chartreuse)" stroke-width="1.5"/>
          <line x1="7" y1="12.5" x2="9" y2="12.5" stroke="var(--chartreuse)" stroke-width="1.5"/>
        </svg>
        <span>602-418-5093</span>
      </div>
      <div class="contact__row">
        <svg class="icon" viewBox="0 0 16 16" aria-hidden="true">
          <circle cx="8" cy="8" r="6.5" fill="none" stroke="var(--chartreuse)" stroke-width="1.4"/>
          <ellipse cx="8" cy="8" rx="2.8" ry="6.5" fill="none" stroke="var(--chartreuse)" stroke-width="1.2"/>
          <line x1="1.5" y1="8" x2="14.5" y2="8" stroke="var(--chartreuse)" stroke-width="1.2"/>
        </svg>
        <span>www.vantorelstone.example</span>
      </div>
    </div>

    <div class="contact contact--right">
      <div class="contact__row">
        <svg class="icon" viewBox="0 0 16 16" aria-hidden="true">
          <path d="M3.5 1.5l2.6 0.2 1 3.2-1.7 1.2c0.8 1.8 2.2 3.2 4 4l1.2-1.7 3.2 1v2.6c0 0.8-0.7 1.5-1.5 1.5C6.6 13.5 2 8.9 2 3c0-0.8 0.7-1.5 1.5-1.5z" fill="var(--chartreuse)"/>
        </svg>
        <span>Fax 602-731-6624</span>
      </div>
      <div class="contact__row">
        <svg class="icon" viewBox="0 0 16 16" aria-hidden="true">
          <rect x="1" y="3" width="14" height="10" fill="var(--chartreuse)"/>
          <polyline points="1,3 8,9 15,3" fill="none" stroke="var(--charcoal)" stroke-width="1.3"/>
        </svg>
        <span>marisol@vantorelstone.example</span>
      </div>
    </div>
  </section>

  <section class="card card--back" aria-label="Business card back">
    <svg class="card__ground" viewBox="0 0 680 389" preserveAspectRatio="none" aria-hidden="true">
      <rect width="680" height="389" fill="var(--charcoal)"/>
      <polygon points="70,0 86,0 20,389 4,389" fill="var(--chartreuse)"/>
      <polygon points="90,0 112,0 46,389 24,389" fill="var(--taupe)"/>
    </svg>
  </section>

</main>
</body>
</html>
```